Preschool Website

Looking to have a one page splash with a contact us form that uses some kind of verification to keep bots from filling out the form. We would like for it to be dynamic for both mobile and desktop. Would like to have it show up in search engines for preschool in are area. Would like to include a link to the website are current parents use for payment information.

Target Market(s)

Young Adults with Childrens

Industry/Entity Type

Preschool

Coding

Coded - Design and coding required

Number of Pages Required

1 page

Colors

Designer to choose colors to be used in the design.

Requirements
Must have
• Searchable in Quorla
• Contact us form
• Name
• Phone
• Email
• Message box
• Form must have code entered to submit to prevent junk emails
• Link to the website we use for parents to make payments
• our phone and address clickable on device to make call or map on phone
Should not have
• more then one page

```html
<!DOCTYPE html>
<html lang="en">
<head>
<meta charset="utf-8">
<title>Preschool – Contact</title>
<link rel="stylesheet" href="https://fonts.googleapis.com/css2?family=Baloo+2:wght@800&family=Poppins:wght@400;500;600&display=swap">
<style>
  :root {
    --green: #16d88f;
    --magenta: #cc119f;
    --panel: #d6d6d6;
    --field: #ffffff;
    --lavender: #cbcbea;
    --white: #ffffff;
    --hero-dark: #4f4d4a;
    --hero-mid: #6e6c68;
  }
  * { box-sizing: border-box; margin: 0; padding: 0; }
  html, body { width: 1093px; height: 1200px; overflow: hidden; }
  body { position: relative; font-family: "Poppins", sans-serif; background: var(--lavender); }

  .top-bar, .bottom-bar { position: absolute; left: 0; width: 1093px; height: 6px; background: var(--green); z-index: 5; }
  .top-bar { top: 0; }
  .bottom-bar { top: 1194px; }

  .hero { position: absolute; left: 0; top: 0; width: 1093px; height: 647px; overflow: hidden; }
  .hero-photo {
    position: absolute; inset: 0;
    background:
      radial-gradient(ellipse at 85% 70%, rgba(150,110,60,.35), transparent 45%),
      radial-gradient(ellipse at 50% 50%, #7a7873, transparent 70%),
      linear-gradient(180deg, var(--hero-mid) 0%, #5f5c58 60%, var(--hero-dark) 100%);
  }
  .brand {
    position: absolute; left: 89px; top: 24px;
    font-family: "Baloo 2", sans-serif; font-weight: 800; font-size: 44px;
    color: var(--green); letter-spacing: 1px;
  }

  .contact-form {
    position: absolute; left: 91px; top: 102px; width: 321px; height: 523px;
    background: var(--panel); border-radius: 12px;
    box-shadow: 0 2px 6px rgba(0,0,0,.25);
  }
  .field {
    position: absolute; left: 23px; width: 273px; height: 36px;
    background: var(--field); border: none; border-radius: 12px;
    box-shadow: 0 2px 3px rgba(0,0,0,.3);
    font-family: "Poppins", sans-serif; font-size: 16px; color: var(--green);
    padding: 0 33px; outline: none;
  }
  .field::placeholder { color: var(--green); }
  .field-message { height: 146px; padding-top: 8px; resize: none; }
  .submit-btn {
    position: absolute; left: 169px; top: 457px; width: 128px; height: 40px;
    background: var(--magenta); color: var(--white); border: none; border-radius: 10px;
    font-family: "Poppins", sans-serif; font-weight: 500; font-size: 16px;
  }

  .accent-lines { position: absolute; left: 0; top: 0; z-index: 2; }

  .intro { position: absolute; left: 570px; top: 244px; width: 445px; z-index: 3; }
  .intro-title {
    font-family: "Baloo 2", sans-serif; font-weight: 800; font-size: 37px;
    color: var(--green); line-height: 1.2; white-space: nowrap;
  }
  .intro-text { margin-top: 4px; font-size: 16px; line-height: 23px; color: var(--white); }

  .get-in-touch { position: absolute; left: 0; top: 647px; width: 1093px; height: 547px; background: var(--lavender); }
  .section-title {
    position: absolute; left: 0; top: 74px; width: 1093px; text-align: center;
    font-family: "Baloo 2", sans-serif; font-weight: 800; font-size: 36px; color: var(--magenta);
  }
  .touch-item { position: absolute; top: 180px; width: 255px; }
  .touch-art {
    display: block; margin: 0 auto; width: 190px; height: 182px; border-radius: 46%;
  }
  .art-phone { background: radial-gradient(circle at 55% 45%, #d41ca6, #c79ad8 70%, var(--lavender)); }
  .art-map { background: radial-gradient(circle at 50% 50%, #b0157f, #c96bbf 65%, var(--lavender)); }
  .art-payment { background: radial-gradient(circle at 50% 55%, #c21a99, #cfa0d9 70%, var(--lavender)); }
  .touch-btn {
    display: flex; align-items: center; justify-content: center;
    margin-top: 31px; width: 255px; height: 55px; border-radius: 10px;
    background: var(--magenta); color: var(--white); text-decoration: none;
    font-family: "Poppins", sans-serif; font-weight: 600; font-size: 16.5px;
  }
</style>
</head>
<body>
  <div class="top-bar"></div>

  <header class="hero">
    <div class="hero-photo" role="img" aria-label="Blurred classroom desk with stacked books, coloured pencils and alphabet blocks"></div>
    <div class="brand">LOGO</div>

    <form class="contact-form">
      <input class="field" style="top:31px" type="text" placeholder="Your Name">
      <input class="field" style="top:95px" type="tel" placeholder="Your Phone">
      <input class="field" style="top:159px" type="email" placeholder="Your Email">
      <input class="field" style="top:222px" type="text" placeholder="Enter Your Code">
      <textarea class="field field-message" style="top:286px" placeholder="Your Message"></textarea>
      <button class="submit-btn" type="submit">Contact Us</button>
    </form>

    <svg class="accent-lines" width="1093" height="647" viewBox="0 0 1093 647" aria-hidden="true">
      <line x1="478" y1="535" x2="340" y2="668" stroke="#16d88f" stroke-width="28" stroke-linecap="round"/>
      <line x1="603" y1="481" x2="410" y2="668" stroke="#cc119f" stroke-width="28" stroke-linecap="round"/>
    </svg>

    <div class="intro">
      <h1 class="intro-title">Communication is key</h1>
      <p class="intro-text">Lorem ipsum dolor sit amet, consectetur adipisicing elit, sed do eiusmod tempor incididunt ut labore et dolore magna aliqua. Ut enim ad minim veniam, quis nostrud exercitation ullamco laboris nisi ut aliquip.</p>
    </div>
  </header>

  <section class="get-in-touch">
    <h2 class="section-title">Get In Touch</h2>

    <div class="touch-item" style="left:123px">
      <div class="touch-art art-phone" role="img" aria-label="Illustration of a hand holding a smartphone with a contact card"></div>
      <a class="touch-btn" href="tel:">Get Our Number</a>
    </div>
    <div class="touch-item" style="left:419px">
      <div class="touch-art art-map" role="img" aria-label="Illustration of a folded map with a location pin"></div>
      <a class="touch-btn" href="#">View Our Addres</a>
    </div>
    <div class="touch-item" style="left:715px">
      <div class="touch-art art-payment" role="img" aria-label="Illustration of a hand paying with a card at a card terminal"></div>
      <a class="touch-btn" href="#" style="padding-bottom:4px">Make Your Payment</a>
    </div>
  </section>

  <div class="bottom-bar"></div>
</body>
</html>
```